Bespoke Builders Business Card Design

We need a business card for an established builder of high quality bespoke homes in Auckland and Northland. We build and renovate homes collaboratively facilitating effective communication between owners, builders, architects, suppliers and tradespeople. We have never built or renovated a home that leaks or has faults. We only use reliable materials. We have never been sued or had legal action taken against us. We are honest builders of bespoke homes not group mass produced homes. Our niche market is in character homes. We practice sustainability and have built a lot of coastal property. We have been in business for over thirty years . We would like to see natural colors of the environment sand,sea and maybe vegetation . The design should communicate quality, sustainability,fair pricing, open communication and the originality of bespoke building. And the fact that the builder is registered.

Industry/Entity Type

Business

Contact Information for Business Card

Rowan Tellick Builders
Ph. 021583917
18 Kestrel Rd Harwood Bay Auckland 0814
PO Box 927 Mangawhai 0583

```html
<!DOCTYPE html>
<html lang="en">
<head>
<meta charset="utf-8">
<title>Rowan Tellick Builders – Business Card</title>
<link rel="stylesheet" href="https://fonts.googleapis.com/css2?family=PT+Serif&family=Open+Sans:wght@400&display=swap">
<style>
  :root {
    --backdrop: #3a3330;
    --card: #000000;
    --frame: #d9c21a;
    --rule: #9a9a9a;
    --ink: #ffffff;
  }
  * { margin: 0; padding: 0; box-sizing: border-box; }
  html, body {
    width: 1200px;
    height: 780px;
    overflow: hidden;
    background: var(--backdrop);
  }
  .canvas {
    position: relative;
    width: 1200px;
    height: 780px;
    display: flex;
    align-items: center;
    justify-content: center;
    gap: 60px;
  }
  .card {
    position: relative;
    width: 525px;
    height: 300px;
    background: var(--card);
    box-shadow: 0 10px 30px rgba(0,0,0,0.45);
  }
  .card__frame {
    position: absolute;
    inset: 20px 24px;
    border: 1.5px solid var(--frame);
  }
  .card__name {
    position: absolute;
    font-family: "PT Serif", Georgia, serif;
    color: var(--ink);
    white-space: nowrap;
    letter-spacing: 0.5px;
  }
  .card__rule {
    position: absolute;
    height: 1.5px;
    background: var(--rule);
  }
  /* Front */
  .card--front .card__name {
    top: 72px;
    left: 140px;
    font-size: 31px;
  }
  .card--front .card__rule--left { top: 70px; left: 0; width: 128px; }
  .card--front .card__rule--right { top: 124px; left: 392px; width: 133px; }
  .card__contact {
    position: absolute;
    top: 150px;
    left: 0;
    width: 100%;
    text-align: center;
    font-family: "Open Sans", Arial, sans-serif;
    font-size: 13px;
    line-height: 1.55;
    color: var(--ink);
    list-style: none;
  }
  /* Back */
  .card--back .card__name {
    top: 108px;
    left: 0;
    width: 100%;
    text-align: center;
    font-size: 34px;
  }
</style>
</head>
<body>
  <main class="canvas">
    <section class="card card--front" aria-label="Card front">
      <div class="card__frame"></div>
      <div class="card__rule card__rule--left"></div>
      <div class="card__rule card__rule--right"></div>
      <h1 class="card__name">Rowan Tellick Builders</h1>
      <ul class="card__contact">
        <li class="card__phone">021583917</li>
        <li class="card__address">18 Kestrel Rd Harwood Bay Auckland 0814</li>
        <li class="card__postal">PO Box 927 Mangawhai 0583</li>
      </ul>
    </section>
    <section class="card card--back" aria-label="Card back">
      <div class="card__frame"></div>
      <h2 class="card__name">Rowan Tellick Builders</h2>
    </section>
  </main>
</body>
</html>
```